Bright Harbor Counseling Letterhead for hip modern business

I would like some ombre use of the colors in the logo hip letterhead that incorporates logo colors and feel, needs to connect with young professionals and college students. i need to be able to write letters to schools to excuse absences as well. i like color blocks on one side preferably using colors from the attached logo design.

Target Market(s)

high income young people, young adults and college students

Industry/Entity Type

mental health

Font styles to use
Serif
Sans Serif

Colors
0054AA
0677BA
7BADD7
CADEEF
E8F1F8
0094D4
00A9DD
6FCCEA
C7EBF8
E9F6FB
00AB8E
00BBA5
67D7C9
C6EFE9
E9F9F6
59FF00
82FF00
B8FF75
E3FFCB
F4FFEA
A7469A
B969AE
D3A5CF
EDDBEB
F8F0F9
6B429C
8869AF
B7A5CE
E3DAEB
F3F0F8

Requirements
Must have
• a modern hip feel, somewhat color

```html
<!DOCTYPE html>
<html lang="en">
<head>
<meta charset="utf-8">
<title>Bright Harbor Counseling Letterhead</title>
<link rel="stylesheet" href="https://fonts.googleapis.com/css2?family=Jost:wght@300&family=Open+Sans:wght@600;700&display=swap">
<style>
  :root {
    --backdrop: #dcdfe0;
    --paper: #ffffff;
    --plum: #a7469a;
    --plum-soft: #b969ae;
    --violet: #6b429c;
    --ocean: #0677ba;
    --sky: #0094d4;
    --sky-light: #6fccea;
    --ink: #2f2f33;
    --ink-soft: #6a6a70;
    --tint-blue: #e9f6fb;
    --tint-lilac: #e3daeb;
    --tint-pink: #f8f0f9;
    --tint-mauve: #eddbeb;
    --rule: #c9c9cc;
  }
  * { box-sizing: border-box; margin: 0; padding: 0; }
  html, body { width: 1200px; height: 784px; overflow: hidden; }
  body {
    background: var(--backdrop);
    display: flex;
    align-items: center;
    justify-content: center;
  }
  .letterhead {
    position: relative;
    width: 572px;
    height: 740px;
    background: var(--paper);
    overflow: hidden;
    box-shadow: 0 2px 10px rgba(0,0,0,.12);
  }
  .corner { position: absolute; inset: 0; width: 572px; height: 740px; }
  .tint { position: absolute; }
  .tint--blue  { left: 398px; top: 188px; width: 58px; height: 44px; background: var(--tint-blue); }
  .tint--lilac { left: 452px; top: 150px; width: 72px; height: 60px; background: var(--tint-lilac); opacity: .7; }
  .tint--mauve { left: 426px; top: 232px; width: 78px; height: 56px; background: var(--tint-mauve); opacity: .8; }
  .tint--pink  { left: 516px; top: 244px; width: 48px; height: 36px; background: var(--tint-pink); }
  .tint--sky   { left: 520px; top: 190px; width: 52px; height: 50px; background: var(--tint-blue); }

  .brand {
    position: absolute;
    right: 66px;
    top: 70px;
    text-align: right;
    font-family: "Jost", sans-serif;
    font-weight: 300;
    color: var(--ink);
  }
  .brand__name { font-size: 27px; line-height: 1; letter-spacing: .2px; }
  .brand__field { font-size: 14px; letter-spacing: 4px; margin-top: 4px; }
  .brand__dot {
    position: absolute;
    right: 36px;
    top: 84px;
    width: 22px;
    height: 22px;
    border-radius: 50%;
    background: var(--plum-soft);
  }

  .contact {
    position: absolute;
    left: 396px;
    top: 160px;
    padding-left: 12px;
    border-left: 1px solid var(--rule);
    font-family: "Open Sans", sans-serif;
    font-size: 8.5px;
    line-height: 13px;
    color: var(--ink-soft);
    font-weight: 600;
  }
  .contact__item { display: flex; align-items: flex-start; gap: 5px; }
  .contact__item--address { color: var(--plum); font-weight: 700; }
  .contact__icon {
    flex: none;
    width: 10px;
    height: 10px;
    margin-top: 1.5px;
    border-radius: 50%;
    background: var(--plum);
    display: flex;
    align-items: center;
    justify-content: center;
  }
  .contact__icon svg { width: 6px; height: 6px; fill: #fff; }
</style>
</head>
<body>
  <main class="letterhead">
    <svg class="corner" viewBox="0 0 572 740" aria-hidden="true">
      <defs>
        <linearGradient id="plumWash" x1="0" y1="0" x2="1" y2="1">
          <stop offset="0" stop-color="#a7469a"/>
          <stop offset="1" stop-color="#b969ae"/>
        </linearGradient>
        <linearGradient id="skyWash" x1="0" y1="0" x2="1" y2="1">
          <stop offset="0" stop-color="#6fccea"/>
          <stop offset="1" stop-color="#0677ba"/>
        </linearGradient>
      </defs>
      <path d="M360 0 H572 V150 C520 60 450 14 360 0 Z" fill="url(#plumWash)"/>
      <path d="M0 560 C36 660 100 724 200 740 H0 Z" fill="url(#skyWash)"/>
    </svg>

    <div class="tint tint--blue"></div>
    <div class="tint tint--lilac"></div>
    <div class="tint tint--sky"></div>
    <div class="tint tint--mauve"></div>
    <div class="tint tint--pink"></div>

    <header class="brand">
      <div class="brand__name">Bright Harbor</div>
      <div class="brand__field">Counseling</div>
    </header>
    <span class="brand__dot"></span>

    <address class="contact">
      <div class="contact__item contact__item--address">
        <span class="contact__icon"><svg viewBox="0 0 10 10"><path d="M5 0a3.5 3.5 0 0 0-3.5 3.5C1.5 6 5 10 5 10s3.5-4 3.5-6.5A3.5 3.5 0 0 0 5 0zm0 5a1.5 1.5 0 1 1 0-3 1.5 1.5 0 0 1 0 3z"/></svg></span>
        <span>0000 Harbor Way, Ste 135,<br>California, 93000, United States</span>
      </div>
      <div class="contact__item">
        <span class="contact__icon"><svg viewBox="0 0 10 10"><path d="M2 0l2 2.5-1 1.2a6 6 0 0 0 3.3 3.3l1.2-1L10 8l-1.5 2C4 10 0 6 0 1.5z"/></svg></span>
        <span>(000) 000-0000</span>
      </div>
      <div class="contact__item">
        <span class="contact__icon"><svg viewBox="0 0 10 10"><path d="M2 0h6v3H2zM0 4h10v4H8v2H2V8H0zm3 3v2h4V7z"/></svg></span>
        <span>(000) 000-0000</span>
      </div>
      <div class="contact__item">
        <span class="contact__icon"><svg viewBox="0 0 10 10"><path d="M0 2h10v6H0zm1 1v.3L5 6l4-2.7V3L5 5.5z"/></svg></span>
        <span>hello@brightharbor.example</span>
      </div>
      <div class="contact__item">
        <span class="contact__icon"><svg viewBox="0 0 10 10"><path d="M5 0a5 5 0 1 0 0 10A5 5 0 0 0 5 0zm0 1.2c.8.8 1.3 2.2 1.3 3.8S5.8 8 5 8.8C4.2 8 3.7 6.6 3.7 5S4.2 2 5 1.2zM1.3 4.5h1.6v1H1.3zm5.8 0h1.6v1H7.1z"/></svg></span>
        <span>www.brightharbor.example</span>
      </div>
    </address>
  </main>
</body>
</html>
```